Open Harbor book needs a cover design

I need a front and back cover design that demonstrates a strong sense of possibility that trust can be repaired even if things look bleak. Repairing trust is difficult, but this book is full of wisdom, proven strategies, and doctoral research to help people strengthen relationships and improve trust. It can help any group: business, nonprofit, education, service. Showing diversity of groups and people is very important. For the cover title, there should be a play on words: "Open Harbor: Is it? Within Reach" should have the words "is it?" crossed out and the words "It IS! should be replaced there in a striking way. Perhaps in red ink. For publishing purposes, book will be titled Open Harbor: It IS Within Reach! Please see the attachment for an example. The book layout is approximately 260 pages.

A business self-help book, but the target is any person in a group that feels they have lost trust in each other. It can be just a normal person struggling in a volunteer group they are a part of, or a supervisor whose group is not working well together. It can be a leader who just wants their group to be stronger.

Business Management

• Allise - I believe is being used on the interior of the book for the title page and headings

• Show hope and possibility in the midst of difficulty. Must have a play on the words in the title "Open Harbor: Is it? Within Reach" with crossing out "is it?" with "It IS!" (see attached example) Must include the author's name: Marla Quentin, PhD Must include a smaller tagline: "Practical Steps to Move Teams Forward Again"
• Showing diverse people, or hands. Diverse kinds of groups - not just business. A colorful cover. Maybe show the complexity of trust when it is broken...broken pieces of trust that are then picked up and put together when people work together. Could show people (or images of hands) or other ways to show that it's a choice and it is possible to repair broken trust. I'd also like to convey a sense of a group - not just random people. That they have something at stake to work on repairing trust together and this book can help them.
• If images of people are used, just showing one gender or race is not okay. Nor just binary choices: like an image containing one man and one woman, or one white person and one person of color - otherwise it seems that the book on Open Harbor is about race or gender relations.

```html
<!DOCTYPE html>
<html lang="en">
<head>
<meta charset="utf-8">
<title>Open Harbor: It IS Within Reach! | Marla Quentin, PhD</title>
<link href="https://fonts.googleapis.com/css2?family=Oranienbaum&family=Cormorant+Garamond:wght@500;600;700&family=Permanent+Marker&display=swap" rel="stylesheet">
<style>
  :root {
    --ink-teal: #1d4f5e;
    --mark-red: #d4362c;
    --sky-left: #8fc3d6;
    --mist-center: #f3ece6;
    --peach-right: #f6c79a;
    --apricot: #f2a56e;
    --photo-frame: #ffffff;
    --photo-cool: #9fb7c9;
    --photo-warm: #c8a98e;
  }
  * { margin: 0; padding: 0; box-sizing: border-box; }
  html, body { width: 763px; height: 1200px; overflow: hidden; }
  body { background: #ffffff; }

  .book-cover {
    position: relative;
    width: 763px;
    height: 1200px;
    overflow: hidden;
    background:
      linear-gradient(180deg, rgba(255,255,255,0.15) 0%, rgba(255,255,255,0) 40%, rgba(120,170,200,0.18) 100%),
      linear-gradient(100deg, var(--sky-left) 0%, #c9dde2 22%, var(--mist-center) 45%, #f8dcc0 68%, var(--peach-right) 85%, var(--apricot) 100%);
  }

  .author-name {
    position: absolute;
    top: 30px;
    left: 0;
    width: 100%;
    text-align: center;
    font-family: "Cormorant Garamond", serif;
    font-weight: 600;
    font-size: 40px;
    letter-spacing: 6px;
    color: var(--ink-teal);
  }

  .title-word {
    position: absolute;
    left: 0;
    width: 100%;
    text-align: center;
    font-family: "Oranienbaum", serif;
    color: var(--ink-teal);
    line-height: 1;
  }
  .title-open { top: 147px; font-size: 180px; letter-spacing: 2px; }
  .title-harbor { top: 300px; font-size: 168px; letter-spacing: 0; }

  .title-correction {
    position: absolute;
    top: 452px;
    left: 0;
    width: 100%;
    text-align: center;
    padding-right: 150px;
    font-family: "Permanent Marker", sans-serif;
    font-size: 36px;
    line-height: 1;
    color: var(--ink-teal);
    letter-spacing: 2px;
    transform: rotate(-2deg);
  }

  .title-reach-line {
    position: absolute;
    top: 497px;
    left: 0;
    width: 100%;
    display: flex;
    justify-content: center;
    align-items: flex-end;
    gap: 6px;
  }
  .struck-phrase {
    position: relative;
    font-family: "Oranienbaum", serif;
    font-size: 40px;
    line-height: 1;
    color: var(--ink-teal);
    padding-bottom: 8px;
  }
  .struck-phrase svg {
    position: absolute;
    left: -4px;
    top: 6px;
  }
  .title-reach {
    font-family: "Oranienbaum", serif;
    font-size: 84px;
    line-height: 1;
    color: var(--ink-teal);
    letter-spacing: 1px;
  }

  .tagline {
    position: absolute;
    top: 662px;
    left: 52px;
    font-family: "Cormorant Garamond", serif;
    font-weight: 600;
    font-size: 22px;
    line-height: 1.3;
    letter-spacing: 1px;
    color: var(--ink-teal);
  }

  .group-photo {
    position: absolute;
    border: 6px solid var(--photo-frame);
    box-shadow: 0 4px 10px rgba(30, 60, 80, 0.25);
  }
  .group-photo-meeting {
    top: 826px;
    left: 38px;
    width: 330px;
    height: 220px;
    transform: rotate(-1deg);
    background: linear-gradient(160deg, #d9e2ea 0%, var(--photo-cool) 45%, var(--photo-warm) 100%);
  }
  .group-photo-huddle {
    top: 764px;
    left: 350px;
    width: 390px;
    height: 205px;
    transform: rotate(1deg);
    background: linear-gradient(200deg, #e6e9ec 0%, #a9c3d0 40%, #6f8fa6 70%, var(--photo-warm) 100%);
  }

  .publisher {
    position: absolute;
    top: 1122px;
    left: 306px;
    display: flex;
    align-items: center;
    gap: 8px;
    font-family: "Cormorant Garamond", serif;
    font-weight: 700;
    color: var(--ink-teal);
  }
  .publisher-square {
    width: 28px;
    height: 28px;
    background: var(--ink-teal);
  }
  .publisher-name {
    font-size: 17px;
    line-height: 1.05;
    letter-spacing: 1px;
  }
</style>
</head>
<body>
  <main class="book-cover">
    <p class="author-name">MARLA QUENTIN, PHD</p>

    <h1 class="book-title">
      <span class="title-word title-open">OPEN</span>
      <span class="title-word title-harbor">HARBOR</span>
      <span class="title-correction">IT IS</span>
      <span class="title-reach-line">
        <span class="struck-phrase">IS IT?
          <svg width="84" height="36" viewBox="0 0 84 36" aria-hidden="true">
            <path d="M2 22 Q40 14 82 16" stroke="#d4362c" stroke-width="4" fill="none" stroke-linecap="round"/>
          </svg>
        </span>
        <span class="title-reach">WITHIN REACH</span>
      </span>
    </h1>

    <p class="tagline">PRACTICAL STEPS<br>TO MOVE TEAMS<br>FORWARD AGAIN</p>

    <div class="group-photo group-photo-meeting" role="img" aria-label="Photo of a diverse team gathered around a meeting table with papers"></div>
    <div class="group-photo group-photo-huddle" role="img" aria-label="Photo of a diverse group of colleagues joining hands over a shared table"></div>

    <div class="publisher">
      <span class="publisher-square"></span>
      <span class="publisher-name">NORTHGATE<br>PRESS</span>
    </div>
  </main>
</body>
</html>
```